Luxury Wine Label for New Startup Winery

We need a wine label for our new winery startup. We have worked with a local designer but do not feel the resulting label / logo have the elevation required to present our brand as a luxury wine. Our winery is called "Quailbrook Vineyards" and we are focused on extremely high quality hand crafted artisan and estate wines from the Pacific Northwest.
We would like to see designs that utilize a tree line, or other imagery that represents the "Quailbrook" part of our company name. Another interesting feature could be wood grain.
A logo will be required based on your design so please design with this in mind:
This logo should be consistent with the wine bottle label design, and should be representative of our high end exclusive wine while giving a sense of place (Oregon/ Pacific Northwest.)
I will supply an image of the design we received from our local designer, PLEASE NOTE: in general we do like wood grain and tree line concepts but feel the execution was poorly done.
ATTN: Logo design should be suitable for use on: Bottles (Red wine/rose/white wine), Bussiness cards, vehicle signage, business signage, etc
P.S.:
If you have a design that is not outside the box we are still interested in seeing it.
Label is for a burgundy style bottle with a label height of 3.5 - 4" and a width of 3.5-4"
any label <= 4"x4" and >=3.5"x3.5" will be acceptable:
HOWEVER Width should be greater than or equal to height due to the bottle format
Target Market(s)
Wine enthusiasts with adequate discretionary budgets to afford $100 bottles of wine.
Industry/Entity Type
Wine / Winery
Requirements
Must have
- A sense of luxury, a feel of exclusivity, and a theme consistent with our product and brand name
Nice to have
- Tree line, wood grain or other wood themes. Serif fonts
Should not have
- anything cheesy, off topic, hard to read script fonts or anything that makes the label hard to read from a few feet away or too busy

```html
<!DOCTYPE html>
<html lang="en">
<head>
<meta charset="utf-8">
<title>Quailbrook Vineyards — Syrah Label</title>
<link rel="stylesheet" href="https://fonts.googleapis.com/css2?family=Cinzel:wght@700&family=Oswald:wght@300;400&display=swap">
<style>
  :root {
    --page: #ffffff;
    --cream: #faf6ea;
    --maroon: #481116;
    --brand-brown: #4a2c2a;
    --origin-red: #a8372c;
    --silhouette: #4d1a1c;
    --text-light: #f1e6e2;
    --gold-light: #f3dd8e;
    --gold-mid: #c9a044;
    --gold-dark: #8a6420;
  }
  * { box-sizing: border-box; margin: 0; padding: 0; }
  html, body {
    width: 1200px; height: 1200px; overflow: hidden;
    background: var(--page);
  }
  .canvas {
    position: relative; width: 1200px; height: 1200px;
  }
  .label {
    position: absolute; left: 100px; top: 239px;
    width: 1000px; height: 722px;
    border-radius: 14px; overflow: hidden;
    background: var(--maroon);
  }
  .label__upper {
    position: absolute; left: 0; top: 0; width: 100%; height: 343px;
    background: var(--cream);
  }
  .brand-square {
    position: absolute; left: 474px; top: 58px;
    width: 52px; height: 52px; background: var(--brand-brown);
  }
  .brand-name {
    position: absolute; left: 0; top: 128px; width: 100%;
    text-align: center;
    font-family: "Cinzel", serif; font-weight: 700;
    color: var(--brand-brown);
    font-size: 31px; line-height: 34px; letter-spacing: 2px;
  }
  .brand-origin {
    position: absolute; left: 0; top: 208px; width: 100%;
    text-align: center;
    font-family: "Oswald", sans-serif; font-weight: 400;
    font-size: 15px; letter-spacing: 0.6px;
    color: var(--origin-red);
  }
  .quail-art {
    position: absolute; left: 680px; top: 185px;
    width: 145px; height: 158px;
    background: linear-gradient(180deg, #6b2f30 0%, var(--silhouette) 100%);
    border-radius: 40px 40px 4px 4px;
  }
  .tagline {
    position: absolute; left: 0; top: 456px; width: 100%;
    text-align: center;
    font-family: "Oswald", sans-serif; font-weight: 400;
    font-size: 16px; letter-spacing: 0.3px;
    color: var(--text-light);
  }
  .varietal {
    position: absolute; left: 0; top: 506px; width: 100%;
    text-align: center;
    font-family: "Cinzel", serif; font-weight: 700;
    font-size: 42px; letter-spacing: 3px; line-height: 50px;
    background: linear-gradient(180deg, var(--gold-light) 0%, var(--gold-mid) 55%, var(--gold-dark) 100%);
    -webkit-background-clip: text; background-clip: text;
    color: transparent;
  }
  .specs {
    position: absolute; left: 0; top: 584px; width: 100%;
    display: flex; justify-content: center; align-items: baseline; gap: 14px;
    font-family: "Oswald", sans-serif; font-weight: 300;
    font-size: 16px; color: var(--text-light);
  }
  .specs__vintage { font-size: 24px; }
</style>
</head>
<body>
  <main class="canvas">
    <section class="label" aria-label="Syrah wine label">
      <div class="label__upper">
        <div class="brand-square" aria-hidden="true"></div>
        <h1 class="brand-name">Quailbrook<br>Vineyards</h1>
        <p class="brand-origin">WILLAMETTE VALLEY, OREGON</p>
        <div class="quail-art" role="img" aria-label="Silhouette of a quail perched on the label band"></div>
      </div>
      <p class="tagline">HAND-CRAFTED ARTISAN ESTATE WINES FROM THE PACIFIC NORTHWEST</p>
      <h2 class="varietal">Syrah</h2>
      <p class="specs">
        <span>750 ml</span><span>/</span>
        <span class="specs__vintage">2024</span><span>/</span>
        <span>13% Alc. Vol.</span>
      </p>
    </section>
  </main>
</body>
</html>
```